South Florida Real Estate Brokerage Business

The name is LAKE VORISSA REAL ESTATE.
The company is a Real estate realty based in Miami.
Is targeted to Latin American clients.
Must express luxury, and efficiency.
Target clients for properties around 250k to a million +.
Vorissa means Royal in Latin.
Should communicate safety and knowledge of the product and transaction with a tech edge.

The web design needs to be a Social tool, with Friendloop and other media integration of some sort. Needs to have a Show case place, a Search place (MLS listings) with maps and filters.
Needs to reflect luxury but also mixed with a social edge capable of engaging clients or transition them to communicate with the page.
Include the logo from the uploaded files, feel free to change the color or font per webdesign.
This is a Front en design, layout and graphics.
Possible future programming if approved.
I can receive Quotes for the Code part.

Spanish and English speakers living in Latin America and Canada looking for apartments and houses to buy.

Business

• Search area.
Neighbourhood area.
Could be a blog or news area.
Client registration.
Social Plugin
• Social linking to networks.
Log in with friendloop account.
Friendloop Like.

```html
<!DOCTYPE html>
<html lang="en">
<head>
<meta charset="utf-8">
<title>Lake Vorissa Real Estate</title>
<link rel="stylesheet" href="https://fonts.googleapis.com/css2?family=Arimo:wght@400;700&family=Open+Sans:wght@400;600;700&display=swap">
<style>
:root{
  --gold:#cbb26c;
  --sky:#4fbfdd;
  --blue:#2aa9d4;
  --blue-deep:#1d7fb3;
  --ink:#2b2b2b;
  --text:#444;
  --line:#d9d9d9;
  --white:#fff;
  --olive:#8a6b00;
  --green:#2f6a12;
  --red:#b22a2a;
}
*{box-sizing:border-box;margin:0;padding:0}
html,body{width:1200px;height:1107px;overflow:hidden;background:var(--white)}
body{font-family:"Arimo",Arial,sans-serif;color:var(--text);position:relative}
.abs{position:absolute}
.top-band{left:0;top:0;width:1200px;height:80px;background:var(--gold)}
.social{right:148px;top:32px;display:flex;gap:10px;align-items:center}
.social a{display:flex;align-items:center;gap:4px;font:600 11px "Open Sans",sans-serif;color:var(--white);text-decoration:none}
.social .dot{width:12px;height:12px;background:#2f5f9e;border-radius:2px}
.brand{left:162px;width:250px;text-align:center;font-family:"Open Sans",sans-serif;font-weight:600;color:var(--ink);white-space:nowrap}
.brand-name{top:92px;font-size:27px;letter-spacing:1px;line-height:32px}
.brand-sub{top:129px;font-size:18px;letter-spacing:2px;line-height:22px}
.brand-rule{left:162px;top:127px;width:250px;height:1px;background:var(--gold)}
.site-search{left:715px;top:89px;display:flex;gap:7px}
.site-search .field{width:293px;height:21px;border:1px solid var(--gold);font-size:11px;font-style:italic;color:#b9b9b9;padding:3px 6px}
.site-search .btn{width:49px;height:21px;background:var(--blue);color:var(--white);font-size:11px;text-align:center;line-height:21px;border-radius:2px}
.nav{left:0;top:189px;width:1200px;height:27px}
.nav a{position:absolute;top:0;height:27px;line-height:29px;text-align:center;font:400 14px "Open Sans",sans-serif;color:var(--ink);text-decoration:none;border-radius:5px 5px 0 0;white-space:nowrap}
.nav a.tab{background:var(--gold)}
.nav-rule{left:0;top:216px;width:1200px;height:4px;background:#e6e6e6}
.hero-band{left:0;top:220px;width:1200px;height:306px;background:var(--sky)}
.hero{left:191px;top:237px;width:815px;height:276px;border:1px solid #e8e8e8;background:linear-gradient(90deg,#c98a2a 0%,#b9704a 30%,#e9e4dc 45%,#2c4a8a 62%,#efe9df 80%,#d7a04a 100%)}
.hero-caption{left:0;bottom:0;width:100%;height:44px;background:rgba(40,40,40,.82);color:var(--white);font:700 12px/17px "Arimo",sans-serif;padding:6px 20px}
.hero-rule{left:0;top:526px;width:1200px;height:5px;background:#e6e6e6}
h1.lead{left:144px;top:549px;font:700 25px "Open Sans",sans-serif;color:var(--ink)}
.ps-icon{left:148px;top:578px;width:30px;height:34px}
.ps-title{left:191px;top:588px;font:400 17px "Open Sans",sans-serif;color:var(--green)}
.label{font:700 11px "Arimo",sans-serif;color:var(--ink)}
.input{border:1px solid #8fb8cf;background:var(--white);height:20px}
.submit{left:414px;top:679px;width:65px;height:22px;background:linear-gradient(#8fe0f5,#3ebfe2);border-radius:3px;color:#0d4f6c;font-size:12px;text-align:center;line-height:22px}
.proposal-title{left:544px;top:548px;font:700 22px "Open Sans",sans-serif;color:var(--blue)}
.proposal-text{left:544px;top:587px;width:211px;font-size:12px;line-height:18px;text-align:justify;color:var(--text)}
.more{font-size:11px;color:var(--blue)}
.login{left:816px;top:543px;width:235px;height:148px;background:var(--sky);border:3px solid #7fd2ea;box-shadow:0 1px 4px rgba(0,0,0,.3);padding:0 10px}
.login h2{font:400 18px "Open Sans",sans-serif;color:var(--red);margin:8px 0 4px}
.login .row{display:flex;align-items:center;margin-top:5px;font-size:12px;color:var(--white);font-weight:700}
.login .row span{width:72px}
.login .row .input{width:138px;border-color:#cde}
.login .ask{font-size:12px;color:var(--red);margin-top:5px}
.login .foot{display:flex;justify-content:space-between;align-items:center;margin-top:4px;font-size:12px;color:var(--red)}
.login .btn{background:var(--blue-deep);color:var(--white);padding:2px 9px;font-size:12px}
.dash{left:156px;top:709px;width:633px;border-top:1px dashed #bbb}
.sec-title{font:700 17px "Open Sans",sans-serif;color:#3a3a3a;display:flex;align-items:center;gap:8px}
.featured-box{left:135px;top:757px;width:657px;height:183px;border:1px solid var(--line);background:linear-gradient(#e3f3fb,#fff 40%)}
.card{position:absolute;top:16px;width:108px}
.card .photo{width:108px;height:77px;border:1px solid #ccc;padding:4px;background:var(--white)}
.card .photo div{width:100%;height:100%;background:linear-gradient(#8cc3ea 0%,#d9d2c4 45%,#a06a4e 65%,#5e9a3c 100%)}
.card h3{font:700 11px "Arimo",sans-serif;color:var(--olive);margin:14px 0 4px}
.card p{font-size:10px;line-height:13px;color:var(--ink)}
.card .vm{display:inline-block;margin-top:8px;background:#ddd;font-size:9px;font-weight:700;color:#555;padding:2px 6px}
.news{left:823px;top:770px;width:232px}
.news p{font-size:11px;line-height:18px;text-align:justify;color:var(--text)}
.news .more{margin-top:2px;line-height:15px}
.news p + .more + p{margin-top:10px}
.footer{left:0;top:952px;width:1200px;height:155px;background:var(--gold)}
.foot-col{font-size:12px;line-height:22px;color:var(--white)}
.contact h4{font:400 17px "Arimo",sans-serif;color:var(--white);margin-bottom:6px}
.contact p{font-size:11px;line-height:18px;color:var(--white)}
</style>
</head>
<body>
<div class="abs top-band"></div>
<div class="abs social">
  <a href="#"><span class="dot"></span>Friendloop</a>
  <a href="#"><span class="dot" style="background:#3aa7d8"></span>Chirpline</a>
  <a href="#"><span class="dot" style="background:#1f6a97"></span>Workweave</a>
</div>
<div class="abs brand brand-name">LAKE VORISSA</div>
<div class="abs brand-rule"></div>
<div class="abs brand brand-sub">REAL ESTATE</div>
<div class="abs site-search"><div class="field">MLS ID, Building Name, Address, City, Zip,Agent Name</div><div class="btn">Search</div></div>

<nav class="abs nav">
  <a style="left:190px;width:62px">Home</a>
  <a class="tab" style="left:260px;width:76px">About Us</a>
  <a class="tab" style="left:340px;width:121px">Search Properties</a>
  <a class="tab" style="left:464px;width:74px">Services</a>
  <a class="tab" style="left:543px;width:72px">Account</a>
  <a class="tab" style="left:619px;width:75px">Blog</a>
  <a class="tab" style="left:698px;width:74px">Contact</a>
</nav>
<div class="abs nav-rule"></div>
<div class="abs hero-band"></div>
<div class="abs hero" role="img" aria-label="Photo of a modern living room with dining table, sofa and tall windows">
  <div class="abs hero-caption">Lorem ipsum dolor sit amet, et vocibus feugait adolescens vim, ad cum adolescens accommodare.<br>Altera feugiat accumautem accommodare.</div>
</div>
<div class="abs hero-rule"></div>

<h1 class="abs lead">Find the best Place for you.</h1>
<svg class="abs ps-icon" viewBox="0 0 30 34" aria-hidden="true"><path d="M15 3 L28 16 H24 V31 H6 V16 H2 Z" fill="var(--red)"/><rect x="12" y="21" width="6" height="10" fill="#fff"/></svg>
<div class="abs ps-title">Property Search</div>
<div class="abs label" style="left:146px;top:626px">Property Type</div>
<div class="abs input" style="left:241px;top:622px;width:239px"></div>
<div class="abs label" style="left:146px;top:652px">city</div>
<div class="abs input" style="left:241px;top:653px;width:239px"></div>
<div class="abs submit">Submit</div>

<div class="abs proposal-title">Todays Proposal</div>
<p class="abs proposal-text">Lorem ipsum dolor sit amet, et vocibus feugait adolescens vim, ad cum adoles-cens accommodare. Altera feugiat accumautem accommodare.</p>
<div class="abs more" style="left:548px;top:673px">Read more</div>

<form class="abs login">
  <h2>Login</h2>
  <div class="row"><span>Email:</span><div class="input"></div></div>
  <div class="row"><span>Password :</span><div class="input"></div></div>
  <div class="ask">Don't Have an Account?</div>
  <div class="foot"><span>Register Now</span><span class="btn">Login</span></div>
  <div style="text-align:right;font-size:12px;color:var(--red)">&#9633; Remember me</div>
</form>

<div class="abs dash"></div>
<div class="abs sec-title" style="left:138px;top:721px">
  <svg width="20" height="20" viewBox="0 0 20 20" aria-hidden="true"><circle cx="10" cy="10" r="9" fill="none" stroke="#aaa" stroke-width="1.5"/><path d="M5.5 10 L9 13.5 L14.5 6.5" fill="none" stroke="#999" stroke-width="2"/></svg>
  Featured Property
</div>
<section class="abs featured-box">
  <div class="card" style="left:17px"><div class="photo"><div role="img" aria-label="Photo of a brick family house"></div></div><h3>Lorem ipsum</h3><p>Lorem ipsum dolor site laudem incorrupte.</p><span class="vm">View more</span></div>
  <div class="card" style="left:143px"><div class="photo"><div role="img" aria-label="Photo of a two-storey suburban house"></div></div><h3>Lorem ipsum</h3><p>Lorem ipsum dolor site laudem incorrupte.</p><span class="vm">View more</span></div>
  <div class="card" style="left:267px"><div class="photo"><div role="img" aria-label="Photo of a red brick house with garden"></div></div><h3>Lorem ipsum</h3><p>Lorem ipsum dolor site laudem incorrupte.</p><span class="vm">View more</span></div>
  <div class="card" style="left:392px"><div class="photo"><div role="img" aria-label="Photo of a white house with fence"></div></div><h3>Lorem ipsum</h3><p>Lorem ipsum dolor site laudem incorrupte.</p><span class="vm">View more</span></div>
  <div class="card" style="left:519px"><div class="photo"><div role="img" aria-label="Photo of a two-storey suburban house"></div></div><h3>Lorem ipsum</h3><p>Lorem ipsum dolor site laudem incorrupte.</p><span class="vm">View more</span></div>
</section>

<div class="abs sec-title" style="left:817px;top:725px">
  <svg width="20" height="20" viewBox="0 0 20 20" aria-hidden="true"><circle cx="10" cy="10" r="9" fill="none" stroke="#aaa" stroke-width="1.5"/><path d="M5.5 10 L9 13.5 L14.5 6.5" fill="none" stroke="#999" stroke-width="2"/></svg>
  Latest News
</div>
<div class="abs news">
  <p>Lorem ipsum dolor sit amet, et vocibus feugait adolescens vim, ad cum adolescens accom-modare. Altera feugiat accumsan.</p>
  <div class="more">Read more</div>
  <p>Lorem ipsum dolor sit amet, et vocibus feugait adolescens vim, ad cum adolescens accom-modare. Altera feugiat accumsan.</p>
  <div class="more">Read more</div>
</div>

<footer class="abs footer">
  <div class="abs foot-col" style="left:161px;top:20px">Home<br>Todays Proposal<br>Propery Management<br>Services Desk</div>
  <div class="abs foot-col" style="left:405px;top:25px">Plans &amp; Pricing<br>FAQ<br>About us<br>Contact Us</div>
  <div class="abs foot-col" style="left:560px;top:26px">Plans &amp; Pricing<br>FAQ<br>About us<br>Contact Us</div>
  <div class="abs contact" style="left:829px;top:22px">
    <h4>Contact &nbsp;us</h4>
    <p>Address: Coral Crest,<br>Lane No.3, Opp. Post office,<br>&nbsp;City: XYZ</p>
    <p style="margin-top:10px">Realestate &copy; 2011 Brightkey Pty Ltd</p>
  </div>
</footer>
</body>
</html>
```